Fun conversation piece for the home depicting the history of the ownership (title) and more!

We need some ideas for a framed display to be hung in a home for a new company I started called Tale of Dwelling, LLC. We will create framed (or unframed canvass) wall displays depicting the Tale of the Dwelling (title transfers) with some interesting background on the subdivision the home is located. This will be a conversation piece. Use color if you feel that works best. I am envisioning perhaps the writing to be in old English or old Spanish font to reflect the history of Florida where I am located. I am wanting to incorporate perhaps a picture of the home converted into sketch as a background to the "history". Or we could skip that and use the vegetation (trees) native to the area for a background. I am going to attach something I found online as a sample but I am open to ideas. The sample is a little formal for what I am trying to do. I may sell these framed or as unframed canvass pictures which might need to be a bit more contemporary. I also need a logo if you have any ideas. TD in some form of old English style perhaps? The document attached labeled "Wrenmarsh" is an example of the content I will be creating for the picture.
Updates

I misspelled "States" in one of the paragraphs. Can you correct that for me? United States. Not "sates". My bad.

Logo Text

Tale of Dwelling (or TD). Surprise me.

```html
<!DOCTYPE html>
<html lang="en">
<head>
<meta charset="utf-8">
<title>Wrenmarsh — Tale of Dwelling</title>
<link rel="stylesheet" href="https://fonts.googleapis.com/css2?family=UnifrakturMaguntia&family=Montserrat:wght@400;700&display=swap">
<style>
  :root {
    --ink: #111;
    --body: #3a3a3a;
    --frame: #000;
    --sky: #4fd3f5;
    --sea: #1fa99a;
    --sand: #d7a47a;
    --panel-top: rgba(236, 250, 253, 0.93);
    --panel-bottom: rgba(248, 245, 242, 0.96);
    --row: #000;
    --row-text: #fff;
  }
  * { margin: 0; padding: 0; box-sizing: border-box; }
  html, body { width: 858px; height: 1200px; overflow: hidden; background: #fff; }
  .canvas {
    position: relative;
    width: 858px; height: 1200px;
    background: var(--frame);
    overflow: hidden;
  }
  .scenery {
    position: absolute; left: 16px; top: 16px; right: 16px; bottom: 16px;
    background: linear-gradient(180deg,
      var(--sky) 0%, #7fdcef 18%, #c9eef0 26%, #e8c9c4 29%,
      var(--sea) 33%, #7cc9c1 38%, #d9ddd6 46%,
      #e7c6a8 52%, var(--sand) 68%, #cfb497 80%,
      #9ad6df 90%, #30c2c9 100%);
  }
  .ornament {
    position: absolute; width: 112px; height: 122px;
    background: radial-gradient(circle at 30% 30%, rgba(0,0,0,0.55), rgba(0,0,0,0) 70%);
  }
  .ornament.tl { left: 16px; top: 16px; }
  .ornament.tr { right: 16px; top: 16px; transform: scaleX(-1); }
  .ornament.bl { left: 16px; bottom: 16px; transform: scaleY(-1); }
  .ornament.br { right: 16px; bottom: 16px; transform: scale(-1,-1); }

  .panel {
    position: absolute; left: 78px; top: 63px; width: 702px; height: 1073px;
    border: 7px solid var(--frame);
    border-radius: 86px;
    background: linear-gradient(180deg, var(--panel-top), var(--panel-bottom));
  }
  .title {
    position: absolute; left: 0; right: 0; top: 78px;
    text-align: center;
    font-family: 'UnifrakturMaguntia', serif;
    font-size: 78px; line-height: 1; letter-spacing: 6px;
    color: var(--ink);
  }
  .story {
    position: absolute; left: 132px; top: 168px; width: 594px;
    font-family: 'Montserrat', sans-serif;
    font-size: 15.6px; line-height: 25.6px;
    color: var(--body);
    text-align: justify;
  }
  .story p + p { margin-top: 8px; }
  .story .lead { font-size: 24px; }

  .homes-heading {
    position: absolute; left: 0; right: 0; top: 740px;
    text-align: center;
    font-family: 'UnifrakturMaguntia', serif;
    font-size: 42px; line-height: 1; letter-spacing: 2px;
    color: var(--ink);
  }
  .title-chain {
    position: absolute; left: 187px; top: 789px; width: 485px;
    list-style: none;
    font-family: 'Montserrat', sans-serif; font-weight: 700;
    font-size: 12.2px; color: var(--row-text);
  }
  .title-chain li {
    height: 20px; margin-bottom: 5px;
    background: var(--row);
    display: flex; align-items: center; justify-content: space-between;
    padding: 0 19px;
    white-space: nowrap;
  }
  .title-chain .dash { display: inline-block; width: 18px; height: 2px; background: var(--row-text); }

  .brand-mark {
    position: absolute; left: 178px; top: 990px;
    display: flex; align-items: center; gap: 10px;
    font-family: 'Montserrat', sans-serif; font-weight: 700;
    font-size: 44px; color: var(--ink);
  }
  .brand-mark .square { width: 22px; height: 22px; background: var(--ink); }

  .presenter {
    position: absolute; left: 318px; width: 370px; top: 1004px;
    text-align: center;
    font-family: 'Montserrat', sans-serif; color: var(--ink);
  }
  .presenter .intro { font-size: 21px; line-height: 26px; }
  .presenter .company { font-size: 27px; font-weight: 700; line-height: 34px; letter-spacing: 0.3px; }
  .presenter .place { font-size: 21px; line-height: 26px; }
</style>
</head>
<body>
<div class="canvas">
  <div class="scenery" role="img" aria-label="Soft blurred beach backdrop with palm fronds, turquoise water and sand"></div>
  <div class="ornament tl" role="img" aria-label="Black scroll corner ornament"></div>
  <div class="ornament tr" role="img" aria-label="Black scroll corner ornament"></div>
  <div class="ornament bl" role="img" aria-label="Black scroll corner ornament"></div>
  <div class="ornament br" role="img" aria-label="Black scroll corner ornament"></div>

  <div class="panel"></div>

  <h1 class="title">Wrenmarsh</h1>

  <div class="story">
    <p><span class="lead">W</span>renmarsh is a neighborhood in the City of Pensacola. Located east of Woodland Heights, Wrenmarsh is bordered by 9th Avenue to the west and 12th Avenue and Carpenter's Creek to the east. Initially developed in 1954, an addition was added in 1956. It is located in a beautiful area of America's 1st Settlement (1559), Pensacola, Florida encompassed with towering pine trees and breathtaking heritage oaks.</p>
    <p>The land comprising Wrenmarsh was originally owned by Mateo Ruvalcaba under a Spanish Land Grant and affirmed by President Elias Whitford on September 7, 1835. Spain relinquished Florida to the United States in 1819 under the Adams-Onis Treaty and lands previously granted to settlers prior thereto were honored if claims were filed and approved by the United States government.</p>
    <p>Through the years, the land changed hands many times but was eventually developed into the Wrenmarsh subdivision in 1954, by Dale Whitcombe, President of Wrenmarsh, Inc. The subdivision contains 63 lots with a beautiful, oak-filled park located just off of Euclid Street.</p>
    <p>Built in 1957 and containing approximately 2606 square feet of living, garage and patio space, the home located at 417 Marigold Street is a trip back in time to when houses were carefully planned catering to modern sensibilities, neither too big nor too small, neither too formal nor too casual.</p>
  </div>

  <h2 class="homes-heading">Tale of Dwellings</h2>

  <ul class="title-chain">
    <li><span>September 9, 1835</span><span class="dash"></span><span>Mateo Ruvalcaba, Spanish Land Grant</span></li>
    <li><span>April 27, 1954</span><span class="dash"></span><span>Wrenmarsh Plat approved by Escambia County</span></li>
    <li><span>April 29, 1957</span><span class="dash"></span><span>Dale Whitcombe, III and Marion W. Whitcombe</span></li>
    <li><span>September 20, 1960</span><span class="dash"></span><span>Loretta Jean Parrish (Conley)</span></li>
    <li><span>February 11, 1966</span><span class="dash"></span><span>Walter N. Brisbane and Evelyn E. Brisbane</span></li>
    <li><span>January 20, 1995</span><span class="dash"></span><span>Grant A. Holloway</span></li>
    <li><span>September 1, 2020</span><span class="dash"></span><span>Grant A. Holloway and Curtis Pemberton Lyle</span></li>
  </ul>

  <div class="brand-mark"><span class="square"></span><span>TD</span></div>

  <div class="presenter">
    <p class="intro">Presented by</p>
    <p class="company">TALE OF DWELLING, LLC</p>
    <p class="place">Wrenmarsh, Florida US</p>
  </div>
</div>
</body>
</html>
```